New Innovative Counselling and psychotherapy Service needs Business Card design

Keep it simple and professional. On one side, just company name and logo (perhaps in all blue) and maybe a tag line.

On other side (all white) my name and Qualifications in centre

Industry/Entity Type

Health And Wellness

Contact Information for Business Card

Dara Whelby
Counsellor & Psychotherapist
BSc (Psychol.), BA, Dip. (Couns. & Psych.), PG.Cert (CBT), FGTrK, ONRE

I will also require Mobile no, Email and web site address of which I'll pass on to final designer.

Font styles to use
Sans Serif

Requirements
Must have
• My Logo Only and please use the colours in logo that is in it.
Should not have
• Any other images

```html
<!DOCTYPE html>
<html lang="en">
<head>
<meta charset="utf-8">
<title>Brightwell Lane – Business Card</title>
<link href="https://fonts.googleapis.com/css2?family=Raleway:wght@400&family=Roboto:wght@400;500&display=swap" rel="stylesheet">
<style>
  :root {
    --backdrop: #d8d3ce;
    --card: #eef0f1;
    --brand-blue: #3a9fd8;
    --brand-green: #7bb042;
    --ink: #2b2b2b;
    --icon-green: #5fa86a;
  }
  * { margin: 0; padding: 0; box-sizing: border-box; }
  html, body {
    width: 1200px;
    height: 1054px;
    overflow: hidden;
    background: var(--backdrop);
  }
  .card {
    position: absolute;
    left: 75px;
    top: 210px;
    width: 1050px;
    height: 634px;
    background: var(--card);
    border-radius: 6px;
    overflow: hidden;
    box-shadow: 0 10px 30px rgba(0,0,0,0.15);
    font-family: "Roboto", Arial, sans-serif;
    color: var(--ink);
  }
  .brand-disc {
    position: absolute;
    left: 0;
    top: 57px;
    width: 500px;
    height: 500px;
    border-radius: 50%;
    background: var(--brand-blue);
  }
  .company-name {
    position: absolute;
    right: 43px;
    top: 58px;
    font-family: "Raleway", Arial, sans-serif;
    font-weight: 400;
    font-size: 53px;
    letter-spacing: -0.5px;
    color: var(--ink);
    white-space: nowrap;
  }
  .person {
    position: absolute;
    right: 43px;
    top: 290px;
    text-align: right;
  }
  .person-name {
    font-weight: 500;
    font-size: 37px;
    color: var(--brand-blue);
    line-height: 46px;
  }
  .person-role,
  .person-credentials {
    font-size: 23px;
    line-height: 31px;
    color: var(--ink);
  }
  .contact-list {
    position: absolute;
    right: 43px;
    top: 466px;
    list-style: none;
    text-align: right;
  }
  .contact-item {
    display: flex;
    justify-content: flex-end;
    align-items: center;
    gap: 16px;
    font-size: 24px;
    line-height: 40px;
    color: var(--ink);
  }
  .contact-icon {
    width: 22px;
    height: 22px;
    flex: none;
  }
</style>
</head>
<body>
  <main class="card">
    <div class="brand-disc"></div>

    <h1 class="company-name">Brightwell Lane</h1>

    <section class="person">
      <h2 class="person-name">Dara Whelby</h2>
      <p class="person-role">Counsellor &amp; Psychotherapist</p>
      <p class="person-credentials">BSc (Psychol.), BA, Dip. (Couns. &amp;<br>Psych.), &nbsp;PG.Cert (CBT), FGTrK, ONRE</p>
    </section>

    <ul class="contact-list">
      <li class="contact-item">
        <span>0987 654 3210</span>
        <svg class="contact-icon" viewBox="0 0 24 24" aria-hidden="true">
          <path fill="var(--icon-green)" d="M3 9c0-3 4-5 9-5s9 2 9 5v2h-5V9c0-1-2-1.5-4-1.5S8 8 8 9v2H3z"/>
          <path fill="var(--icon-green)" d="M7 12h10l3 8H4z"/>
        </svg>
      </li>
      <li class="contact-item">
        <span>dara.w@BrightwellLane.com</span>
        <svg class="contact-icon" viewBox="0 0 24 24" aria-hidden="true">
          <rect x="2" y="5" width="20" height="14" rx="1.5" fill="var(--icon-green)"/>
          <path d="M3 6l9 7 9-7" fill="none" stroke="var(--card)" stroke-width="1.8"/>
        </svg>
      </li>
      <li class="contact-item">
        <span>www.BrightwellLane.com</span>
        <svg class="contact-icon" viewBox="0 0 24 24" aria-hidden="true">
          <circle cx="12" cy="12" r="10" fill="var(--icon-green)"/>
          <g fill="none" stroke="var(--card)" stroke-width="1.4">
            <ellipse cx="12" cy="12" rx="4.5" ry="10"/>
            <line x1="2" y1="12" x2="22" y2="12"/>
            <line x1="12" y1="2" x2="12" y2="22"/>
          </g>
        </svg>
      </li>
    </ul>
  </main>
</body>
</html>
```